Website Refresh

I'm looking to refresh my Squarespace website. www.derekmulvane.com

I am pretty happy with the content but would like a better navigation bar, livelier color choices, consistent type faces, and a more modern look. I am willing to pay extra to implement suggested improvements that would make the site more appealing

```html
<!DOCTYPE html>
<html lang="en">
<head>
<meta charset="utf-8">
<title>Keystone – Derek Mulvane</title>
<link href="https://fonts.googleapis.com/css2?family=Poppins:wght@400;500;600&family=Roboto:wght@400;500&display=swap" rel="stylesheet">
<style>
:root{
  --purple:#2e0d54;
  --purple-deep:#260a47;
  --gold:#e8c467;
  --ink:#222;
  --muted:#555;
  --white:#fff;
  --black:#000;
}
*{margin:0;padding:0;box-sizing:border-box}
html,body{width:1200px;height:3315px;overflow:hidden}
body{position:relative;font-family:"Poppins",sans-serif;color:var(--ink);background:var(--white)}
.abs{position:absolute}
.btn{position:absolute;background:var(--gold);color:var(--purple);font-weight:600;font-size:14px;border-radius:22px;display:flex;align-items:center;justify-content:center;text-transform:uppercase}

/* header */
.header{left:0;top:0;width:1200px;height:103px;background:var(--white)}
.brand{left:111px;top:30px;display:flex;align-items:center;gap:10px}
.brand-mark{width:26px;height:26px;background:var(--purple);display:block}
.brand-name{font-size:28px;font-weight:500;color:var(--ink);line-height:1}
.brand-tag{left:111px;top:66px;font-size:10px;color:var(--muted);line-height:1.3;width:200px}
.social{top:38px;display:flex;gap:5px;left:626px}
.social span{width:28px;height:28px;border-radius:50%;display:block}
.lang{left:756px;top:43px;font-size:13px;font-weight:500;display:flex;align-items:center;gap:6px}
.flag{width:28px;height:28px;border-radius:50%;background:linear-gradient(#b22 0 14%,#fff 14% 28%,#b22 28% 42%,#fff 42% 56%,#b22 56% 70%,#fff 70% 84%,#b22 84%)}
.callbox{left:862px;top:26px;display:flex;align-items:center;gap:12px}
.call-label{font-size:15px;font-weight:500}
.call-num{font-size:21px;font-weight:500;line-height:1.1}

/* nav */
.nav{left:0;top:103px;width:1200px;height:58px;background:var(--purple);display:flex;justify-content:center;align-items:center;gap:24px}
.nav a{color:var(--white);font-size:13px;font-weight:600;text-decoration:none;text-transform:uppercase}

/* hero */
.hero{left:0;top:161px;width:1200px;height:625px;background:linear-gradient(135deg,#4a4540,#2d2a2a 45%,#5a4a3e)}
.hero-shade{left:0;top:0;width:100%;height:100%;background:rgba(0,0,0,.28)}
.hero-title{left:0;top:188px;width:1200px;text-align:center;color:var(--white);font-size:40px;font-weight:600}
.hero-sub{left:300px;top:254px;width:600px;text-align:center;color:var(--white);font-size:15px;font-weight:500;line-height:1.75}
.arrow{width:46px;height:46px;border-radius:50%;background:rgba(255,255,255,.35);display:flex;align-items:center;justify-content:center;top:261px}

/* membership */
.member{left:0;top:786px;width:1200px;height:483px;background:var(--purple)}
.member h2{position:absolute;left:111px;top:94px;color:var(--white);font-size:40px;font-weight:500;line-height:1.18;width:560px}
.member ul{position:absolute;left:111px;top:214px;list-style:none}
.member li{color:var(--white);font-size:16px;height:34.5px;display:flex;align-items:center;gap:20px}
.video-main{left:683px;top:696px;width:409px;height:504px;border:3px solid var(--white);background:linear-gradient(160deg,#cfd6e8,#8c88b8 60%,#5d567f)}
.play{position:absolute;border-radius:50%;display:flex;align-items:center;justify-content:center}

/* intro */
.lead{left:0;top:1365px;width:1200px;text-align:center;font-size:22px;font-weight:500;line-height:1.17;color:var(--ink)}
.lead p+p{margin-top:26px}
.intro-photo{left:112px;top:1530px;width:462px;height:281px;border-radius:6px;background:linear-gradient(135deg,#6d6b68,#3a3836 60%,#807a70)}
.intro-text{left:599px;top:1524px;width:490px;font-size:13.3px;line-height:21.5px;color:var(--muted)}
.intro-text p+p{margin-top:21px}

/* panels */
.panel{top:1915px;width:400px;height:406px}
.panel-caption{position:absolute;left:0;width:100%;text-align:center;color:var(--white);font-size:22px;font-weight:500;bottom:48px}
.panel-mid{left:400px;background:var(--purple-deep);text-align:center;color:var(--white)}
.panel-mid h3{position:absolute;top:90px;width:100%;font-size:22px;font-weight:500}
.panel-mid p{position:absolute;top:142px;left:62px;width:276px;font-size:15px;line-height:26px}

/* testimonials */
.t-title{left:0;top:2412px;width:1200px;text-align:center;font-size:38px;font-weight:600;color:var(--ink)}
.t-card{top:2487px;width:313px;height:223px;background:linear-gradient(160deg,#9fb19a,#3f4e7a 65%,#2a3254)}

/* footer */
.footer{left:0;top:2812px;width:1200px;height:503px;background:var(--black);font-family:"Roboto",sans-serif;color:var(--white)}
.footer h4{position:absolute;font-size:19px;font-weight:500;top:106px;color:var(--white)}
.field{position:absolute;background:var(--white);font-size:13px;color:#555;padding:0 18px;display:flex;align-items:center}
.submit{position:absolute;left:112px;top:345px;width:134px;height:45px;background:var(--gold);color:var(--purple-deep);border-radius:24px;font-weight:500;font-size:15px;display:flex;align-items:center;justify-content:center}
.links{position:absolute;left:649px;top:156px;list-style:none;font-size:15px;color:var(--white)}
.links li{height:30px;display:flex;align-items:center;gap:12px}
.contact{position:absolute;left:846px;top:155px;font-size:15px;width:240px;color:var(--white)}
.contact div{display:flex;gap:14px;align-items:flex-start;line-height:24px}
.stay{position:absolute;left:649px;top:364px;font-size:18px;font-weight:500;display:flex;align-items:center;gap:32px}
.stay i{display:inline-block;width:32px;height:32px;border-radius:50%;margin-right:6px;vertical-align:middle}
.rule{position:absolute;left:111px;top:428px;width:978px;height:1px;background:#333}
.copy{position:absolute;left:0;top:446px;width:1200px;text-align:center;font-size:15px;color:var(--white)}
</style>
</head>
<body>

<header class="header abs">
  <div class="brand abs"><span class="brand-mark"></span><span class="brand-name">Keystone</span></div>
  <div class="brand-tag abs">Peer boards for leaders of growing firms.</div>
  <div class="social abs"><span style="background:#3b5998"></span><span style="background:#1da1f2"></span><span style="background:#dd4b39"></span></div>
  <div class="lang abs">Eng
    <svg width="9" height="6" viewBox="0 0 9 6"><path d="M1 1l3.5 3.5L8 1" stroke="#333" fill="none" stroke-width="1.4"/></svg>
    <span class="flag"></span>
  </div>
  <div class="callbox abs">
    <svg width="48" height="48" viewBox="0 0 48 48"><circle cx="24" cy="24" r="22" fill="none" stroke="#2e0d54" stroke-width="3"/><path d="M16 14c2-2 4 0 5 2l1 3c0 1-1 2-2 3 1 3 3 5 6 6 1-1 2-2 3-2l3 1c2 1 4 3 2 5-3 3-7 3-12-1s-9-11-6-17z" fill="#2e0d54"/></svg>
    <div><div class="call-label">Call us Today :</div><div class="call-num">+1 888 888 8888</div></div>
  </div>
</header>

<nav class="nav abs">
  <a>About</a><a>Member Video Testimonials</a><a>Testimonials</a><a>Success Stories</a><a>Derek's Blog</a><a>Derek Mulvane Bio</a><a>Join the Group</a>
</nav>

<section class="hero abs" role="img" aria-label="Photo of executives in a group discussion in an office">
  <div class="hero-shade abs"></div>
  <h1 class="hero-title abs">Turning Good CEOs Into Great CEOs</h1>
  <p class="hero-sub abs">Our award winning CEOs will help you make better decisions for your company, family, and community .</p>
  <div class="btn" style="left:532px;top:328px;width:135px;height:41px">Get Started</div>
  <div class="arrow abs" style="left:68px"><svg width="10" height="10"><path d="M7 1L3 5l4 4" stroke="#333" fill="none" stroke-width="1.5"/></svg></div>
  <div class="arrow abs" style="left:1084px"><svg width="10" height="10"><path d="M3 1l4 4-4 4" stroke="#333" fill="none" stroke-width="1.5"/></svg></div>
</section>

<section class="member abs">
  <h2>Membership is by invitation only for those who:</h2>
  <ul>
    <li><svg width="14" height="14"><circle cx="7" cy="7" r="7" fill="#fff"/><path d="M3.5 7l2.5 2.5 4.5-5" stroke="#2e0d54" stroke-width="1.8" fill="none"/></svg>Open to being challenged</li>
    <li><svg width="14" height="14"><circle cx="7" cy="7" r="7" fill="#fff"/><path d="M3.5 7l2.5 2.5 4.5-5" stroke="#2e0d54" stroke-width="1.8" fill="none"/></svg>Commit to double-digit growth</li>
    <li><svg width="14" height="14"><circle cx="7" cy="7" r="7" fill="#fff"/><path d="M3.5 7l2.5 2.5 4.5-5" stroke="#2e0d54" stroke-width="1.8" fill="none"/></svg>Ongoing learning</li>
    <li><svg width="14" height="14"><circle cx="7" cy="7" r="7" fill="#fff"/><path d="M3.5 7l2.5 2.5 4.5-5" stroke="#2e0d54" stroke-width="1.8" fill="none"/></svg>Giving &amp; receiving honest feedback.</li>
  </ul>
</section>

<div class="video-main abs" role="img" aria-label="Video still of Derek Mulvane speaking in his office">
  <div class="play" style="left:166px;top:213px;width:74px;height:74px;background:rgba(232,196,103,.5)">
    <div class="play" style="position:static;width:58px;height:58px;background:var(--gold)"><svg width="16" height="18"><path d="M2 1l13 8-13 8z" fill="#2e0d54"/></svg></div>
  </div>
</div>

<section class="lead abs">
  <p>If you are lonely with no one you can trust to talk through tough decisions<br>If you don’t have the right people in the right seats</p>
  <p>If you seek financial independence, professional and personal growth, and<br>avoiding burnout; our group might be right for you.</p>
</section>

<div class="intro-photo abs" role="img" aria-label="Photo of a peer advisory group meeting around a conference table"></div>
<div class="intro-text abs">
  <p>After many years in the business world as the founder/CEO of six for-profit and five not-for-profit corporations, I understand the huge responsibility you have for making the right decisions for your company, the personal well-being of your employees and yourself.</p>
  <p>Our Keystone group is made up of 15 other smart CEOs who have been where you are. &nbsp;We meet monthly in a safe, confidential environment to discuss critical business decisions, opportunities, and challenges. Additionally I meet with each member two hours/monthly for a private coaching session.</p>
</div>
<div class="btn" style="left:599px;top:1771px;width:135px;height:41px">Learn More</div>

<section class="panel abs" style="left:0;background:linear-gradient(160deg,#5a6a6a,#2e3a3a 60%,#3b3030)" role="img" aria-label="Group photo of peer CEOs">
  <div class="panel-caption">Impressive Peer CEOs</div>
</section>
<section class="panel panel-mid abs">
  <h3>Seasoned Leader</h3>
  <p>My purpose is to use my gifts and life lessons to help ignite, inspire and transform the lives of leaders of leaders.</p>
  <div class="btn" style="left:86px;top:268px;width:229px;height:41px;font-size:13.5px">Derek Mulvane Biography ›</div>
</section>
<section class="panel abs" style="left:800px;background:linear-gradient(180deg,#f2f2f2,#9a9a9a 60%,#4e4e4e)" role="img" aria-label="Chart comparing member company growth with nonmember companies">
  <div class="panel-caption">Proven Keystone Methodology</div>
</section>

<h2 class="t-title abs">MEMBER VIDEO TESTIMONIALS</h2>
<div class="t-card abs" style="left:112px" role="img" aria-label="Video testimonial from a member company president"><div class="play" style="left:124px;top:79px;width:64px;height:64px;background:rgba(46,13,84,.75)"><svg width="14" height="16"><path d="M1 1l12 7-12 7z" fill="#e8c467"/></svg></div></div>
<div class="t-card abs" style="left:444px" role="img" aria-label="Video testimonial from a member CEO"><div class="play" style="left:124px;top:79px;width:64px;height:64px;background:rgba(46,13,84,.75)"><svg width="14" height="16"><path d="M1 1l12 7-12 7z" fill="#e8c467"/></svg></div></div>
<div class="t-card abs" style="left:775px" role="img" aria-label="Video testimonial from a member company president"><div class="play" style="left:124px;top:79px;width:64px;height:64px;background:rgba(46,13,84,.75)"><svg width="14" height="16"><path d="M1 1l12 7-12 7z" fill="#e8c467"/></svg></div></div>

<footer class="footer abs">
  <h4 style="left:111px">GET IN TOUCH</h4>
  <div class="field" style="left:112px;top:156px;width:234px;height:38px">First Name</div>
  <div class="field" style="left:354px;top:156px;width:235px;height:38px">Last Name</div>
  <div class="field" style="left:112px;top:204px;width:234px;height:38px">Email</div>
  <div class="field" style="left:354px;top:204px;width:235px;height:38px">phone number</div>
  <div class="field" style="left:112px;top:254px;width:477px;height:74px;align-items:flex-start;padding-top:10px">Message</div>
  <div class="submit">SUBMIT</div>

  <h4 style="left:649px">QUICK LINKS</h4>
  <ul class="links">
    <li>»<span>Home</span></li><li>»<span>About Us</span></li><li>»<span>Meet Our Staff</span></li><li>»<span>Our Services</span></li><li>»<span>Testimonials</span></li><li>»<span>Contact Us</span></li>
  </ul>

  <h4 style="left:846px">CONTACT US</h4>
  <div class="contact">
    <div><svg width="12" height="16" style="margin-top:4px"><path d="M6 0a6 6 0 016 6c0 4-6 10-6 10S0 10 0 6a6 6 0 016-6z" fill="#fff"/><circle cx="6" cy="6" r="2.2" fill="#000"/></svg><span>Lorem ipsum dolor sit amet, consectetur adipi</span></div>
    <div style="margin-top:26px"><svg width="12" height="16" style="margin-top:4px"><rect x="1" y="0" width="10" height="16" rx="2" fill="#fff"/><rect x="3" y="2" width="6" height="10" fill="#000"/></svg><span>+1 888 888 8888</span></div>
    <div style="margin-top:14px"><svg width="16" height="12" style="margin-top:6px"><rect x=".75" y=".75" width="14.5" height="10.5" fill="none" stroke="#fff" stroke-width="1.5"/><path d="M1 1l7 6 7-6" stroke="#fff" stroke-width="1.5" fill="none"/></svg><span>info@companyname.com</span></div>
  </div>

  <div class="stay">STAY CONNECTED :<span><i style="background:#3b5998"></i><i style="background:#c13584"></i></span></div>
  <div class="rule"></div>
  <div class="copy">© 2022 Company Name &nbsp;| All Rights Reserved | Terms and Conditions</div>
</footer>

</body>
</html>
```